Business card - Harbor Crest Builders

Design a business card utilizing the given logo.
colors we like: Black, greys, Teal, blues.
Tri color card, horizontal orientation likely
Logo and name likely best on top.
Info on card:

Dennis Farrow
#8 - 4815 Alder Ridge Blvd.
Surrey, B.C. V3K 2R9

778.555.0193
dennisfarrow@tellmail.ca

Slogan: "Building Dreams"

We are a construction company that specializes in new home construction on the West coast of BC Canada. Open Concepts designs of high end homes.

```html
<!DOCTYPE html>
<html lang="en">
<head>
<meta charset="utf-8">
<title>Harbor Crest Builders – Business Card</title>
<link href="https://fonts.googleapis.com/css2?family=Michroma&family=Montserrat:wght@400;500;600&display=swap" rel="stylesheet">
<style>
  :root {
    --backdrop: #5e5e5e;
    --card-white: #ffffff;
    --teal: #06b0a0;
    --ink: #111111;
    --text-light: #ffffff;
  }
  * { margin: 0; padding: 0; box-sizing: border-box; }
  html, body {
    width: 1200px;
    height: 1000px;
    overflow: hidden;
    background: var(--backdrop);
  }
  .canvas {
    position: relative;
    width: 1200px;
    height: 1000px;
  }
  .business-card {
    position: absolute;
    left: 160px;
    top: 228px;
    width: 880px;
    height: 544px;
    background: var(--teal);
    box-shadow: 0 10px 30px rgba(0,0,0,0.35);
    overflow: hidden;
  }
  .brand-band {
    height: 198px;
    background: var(--card-white);
    display: flex;
    align-items: center;
    justify-content: center;
    gap: 22px;
  }
  .brand-dot {
    width: 68px;
    height: 68px;
    border-radius: 50%;
    background: var(--ink);
  }
  .brand-name {
    font-family: "Montserrat", sans-serif;
    font-weight: 600;
    font-size: 42px;
    color: var(--ink);
    letter-spacing: 1px;
    text-transform: uppercase;
  }
  .person {
    position: absolute;
    left: 470px;
    top: 238px;
    color: var(--text-light);
  }
  .person-name {
    font-family: "Michroma", sans-serif;
    font-size: 32px;
    letter-spacing: 1px;
    line-height: 1.2;
  }
  .person-title {
    font-family: "Montserrat", sans-serif;
    font-weight: 500;
    font-size: 21px;
    margin-top: 6px;
  }
  .contact-list {
    position: absolute;
    left: 78px;
    top: 388px;
    list-style: none;
    font-family: "Montserrat", sans-serif;
    font-weight: 500;
    font-size: 22px;
    color: var(--text-light);
  }
  .contact-item {
    display: flex;
    align-items: center;
    gap: 14px;
    height: 32px;
  }
  .contact-icon {
    width: 22px;
    height: 22px;
    flex: none;
  }
</style>
</head>
<body>
<div class="canvas">
  <div class="business-card">
    <header class="brand-band">
      <span class="brand-dot"></span>
      <span class="brand-name">Harbor Crest Builders</span>
    </header>

    <div class="person">
      <div class="person-name">Dennis Farrow</div>
      <div class="person-title">Managing Director</div>
    </div>

    <ul class="contact-list">
      <li class="contact-item">
        <svg class="contact-icon" viewBox="0 0 22 22" aria-hidden="true">
          <rect width="22" height="22" rx="4" fill="#fff"/>
          <path d="M7 4.5c1 0 1.6 2.6 1.6 3.2 0 .8-1.2 1-1 1.8.4 1.6 2.2 3.5 3.8 4 .8.2 1-1 1.8-1 .6 0 3.3.6 3.3 1.6 0 1.3-1.5 3-3 3C8.8 17.1 4.9 13.2 4.9 8 4.9 6.3 5.8 4.5 7 4.5z" fill="var(--teal)"/>
        </svg>
        <span>778.555.0193</span>
      </li>
      <li class="contact-item">
        <svg class="contact-icon" viewBox="0 0 22 22" aria-hidden="true">
          <rect width="22" height="22" rx="4" fill="#fff"/>
          <rect x="4.5" y="6.5" width="13" height="9" rx="1.5" fill="none" stroke="var(--teal)" stroke-width="1.8"/>
          <path d="M4.8 7.2 11 11.6l6.2-4.4" fill="none" stroke="var(--teal)" stroke-width="1.6"/>
        </svg>
        <span>dennisfarrow@tellmail.ca</span>
      </li>
      <li class="contact-item">
        <svg class="contact-icon" viewBox="0 0 22 22" aria-hidden="true">
          <rect width="22" height="22" rx="4" fill="#fff"/>
          <path d="M11 3.8a5 5 0 0 0-5 5c0 3.6 5 9.4 5 9.4s5-5.8 5-9.4a5 5 0 0 0-5-5z" fill="var(--teal)"/>
          <circle cx="11" cy="8.8" r="1.9" fill="#fff"/>
        </svg>
        <span>#8 - 4815 Alder Ridge Blvd. Surrey, B.C. V3K 2R9</span>
      </li>
    </ul>
  </div>
</div>
</body>
</html>
```